Corporate Business Card

Very professional, Modern, Not to busy, include phone address email, website
(253) 617-4930, 18761 52nd Avenue S, Kent, WA 98047, martin@plumlinegroup.com, varkoworks.com

Target Market(s)

Manufacturing

Industry/Entity Type

Aero, machining, manufacturing, Off road racing

Contact Information for Business Card

Phone, address email, website

```html
<!DOCTYPE html>
<html lang="en">
<head>
<meta charset="utf-8">
<title>Varko Works – Business Card</title>
<link rel="stylesheet" href="https://fonts.googleapis.com/css2?family=Arimo:wght@400;700&display=swap">
<style>
  :root {
    --page: #e4e3e0;
    --navy: #22356a;
    --navy-deep: #1d2d5c;
    --steel: #5471b4;
    --red: #d0141c;
    --white: #ffffff;
  }
  html, body {
    margin: 0;
    width: 1200px;
    height: 801px;
    overflow: hidden;
    background: var(--page);
    font-family: "Arimo", Arial, sans-serif;
  }
  .sheet {
    position: relative;
    width: 1200px;
    height: 801px;
  }
  .card {
    position: absolute;
    top: 250px;
    width: 525px;
    height: 300px;
    background: var(--navy);
    overflow: hidden;
    box-shadow: 0 10px 24px rgba(0,0,0,0.22);
  }
  .card--front { left: 50px; }
  .card--back { left: 625px; }

  .brand {
    position: absolute;
    color: var(--white);
    font-weight: 700;
    letter-spacing: 1px;
    white-space: nowrap;
    line-height: 1;
  }
  .brand-rule {
    position: absolute;
    height: 1px;
    background: var(--white);
  }
  .card--front .brand { left: 230px; top: 42px; font-size: 40px; }
  .card--front .brand-rule--short { left: 230px; top: 98px; width: 150px; }

  .identity { position: absolute; left: 30px; top: 114px; }
  .identity__name {
    color: var(--red);
    font-size: 18px;
    line-height: 22px;
    font-weight: 400;
    letter-spacing: 0.5px;
    margin: 0;
  }
  .identity__title {
    color: var(--white);
    font-size: 14px;
    line-height: 18px;
    margin: 2px 0 0;
  }
  .card--front .brand-rule--long { left: 30px; top: 166px; width: 465px; }

  .contact-list {
    position: absolute;
    left: 30px;
    top: 180px;
    margin: 0;
    padding: 0;
    list-style: none;
    color: var(--white);
    font-size: 14px;
  }
  .contact-list li {
    display: flex;
    align-items: center;
    gap: 10px;
    height: 26px;
  }
  .contact-list svg { width: 14px; height: 14px; fill: var(--red); flex: none; }

  .address {
    position: absolute;
    right: 30px;
    top: 186px;
    color: var(--white);
    font-size: 14px;
    line-height: 1.4;
    text-align: right;
    font-style: normal;
  }

  .back-band { position: absolute; inset: 0; width: 100%; height: 100%; }
  .card--back .brand { left: 245px; top: 152px; font-size: 40px; }
  .card--back .brand-rule--short { left: 245px; top: 208px; width: 150px; }
</style>
</head>
<body>
<main class="sheet">

  <section class="card card--front" aria-label="Card front">
    <div class="brand">Varko Works</div>
    <div class="brand-rule brand-rule--short"></div>

    <div class="identity">
      <h1 class="identity__name">DANIEL REYES</h1>
      <p class="identity__title">Manager</p>
    </div>
    <div class="brand-rule brand-rule--long"></div>

    <ul class="contact-list">
      <li>
        <svg viewBox="0 0 24 24" aria-hidden="true"><path d="M6.6 10.8a15 15 0 0 0 6.6 6.6l2.2-2.2a1 1 0 0 1 1-.25 11.4 11.4 0 0 0 3.6.57 1 1 0 0 1 1 1V20a1 1 0 0 1-1 1A17 17 0 0 1 3 4a1 1 0 0 1 1-1h3.5a1 1 0 0 1 1 1c0 1.25.2 2.45.57 3.57a1 1 0 0 1-.25 1z"/></svg>
        (253) 617-4930
      </li>
      <li>
        <svg viewBox="0 0 24 24" aria-hidden="true"><path d="M2 5h20v14H2z M3 6l9 7 9-7" stroke="#22356a" stroke-width="1.5"/></svg>
        martin@plumlinegroup.com
      </li>
      <li>
        <svg viewBox="0 0 24 24" aria-hidden="true"><circle cx="12" cy="12" r="10"/><path d="M2 12h20M12 2c3 3 3 17 0 20M12 2c-3 3-3 17 0 20" stroke="#22356a" stroke-width="1.5" fill="none"/></svg>
        www.varkoworks.com
      </li>
    </ul>

    <address class="address">18761 52nd Avenue S<br>Kent, WA 98047</address>
  </section>

  <section class="card card--back" aria-label="Card back">
    <svg class="back-band" viewBox="0 0 525 300" preserveAspectRatio="none" aria-hidden="true">
      <polygon points="150,300 200,300 200,90 300,70 335,0 290,0 255,55 150,75" fill="var(--steel)"/>
      <polygon points="0,0 290,0 255,55 150,75 150,300 0,300" fill="var(--navy-deep)"/>
    </svg>
    <div class="brand">Varko Works</div>
    <div class="brand-rule brand-rule--short"></div>
  </section>

</main>
</body>
</html>
```